RWT Fittings Ltd Business Cards

We need a business card with our business logo. We provide window and door installations on high-rises in west coast British Colombia, Canada.

I would like my business information and details on one side of the card, and the other side the company name with logo

Target Market(s)

General Contractors

Industry/Entity Type

Construction

Contact Information for Business Card

one side i want my company name and logo in the dark theme logo that i provided

Requirements
Must have
• Marco Peltieri, 16045518293, RWTFittings@mailbox-demo.com, 1407-5194 Linden Row Burnaby BC, V5H 2K9, Owner & Manager

```html
<!DOCTYPE html>
<html lang="en">
<head>
<meta charset="utf-8">
<title>RWT Fittings Ltd Business Card</title>
<link href="https://fonts.googleapis.com/css2?family=Poppins:wght@300;400;600;700&display=swap" rel="stylesheet">
<style>
  :root {
    --backdrop: #1c1c1c;
    --card-white: #ffffff;
    --card-dark: #2a2a2a;
    --brand-blue: #29a8e0;
    --text-grey: #555555;
    --faint-grey: #f1f1f1;
    --mark-grey: #8f8f8f;
  }
  * { margin: 0; padding: 0; box-sizing: border-box; }
  html, body { width: 1200px; height: 897px; overflow: hidden; }
  body { background: var(--backdrop); font-family: 'Poppins', sans-serif; position: relative; }

  .card {
    position: absolute; left: 303px; width: 595px; height: 338px;
    border-radius: 20px; overflow: hidden;
  }
  .card--front { top: 92px; background: var(--card-white); }
  .card--back {
    top: 469px;
    background: radial-gradient(ellipse at 60% 45%, #353535 0%, var(--card-dark) 60%, #222 100%);
  }

  .name-band {
    position: absolute; left: 0; top: 37px; width: 360px; height: 62px;
    background: var(--brand-blue); color: #fff; padding: 10px 0 0 38px;
  }
  .name-band .person { font-weight: 700; font-size: 23px; line-height: 1.1; letter-spacing: 0.3px; }
  .name-band .role { font-weight: 300; font-size: 14px; line-height: 1.2; }

  .brand {
    position: absolute; display: flex; align-items: center; gap: 8px;
    font-weight: 600; white-space: nowrap;
  }
  .brand .brand-square { display: block; flex: none; }
  .card--front .brand { left: 366px; top: 40px; height: 56px; color: var(--brand-blue); font-size: 15px; }
  .card--front .brand-square { width: 40px; height: 40px; background: var(--brand-blue); }
  .card--back .brand { left: 121px; top: 128px; color: var(--mark-grey); font-size: 32px; gap: 16px; }
  .card--back .brand-square { width: 82px; height: 82px; background: #111; }

  .faint-mark {
    position: absolute; left: 37px; top: 145px; width: 140px; height: 155px;
    background: var(--faint-grey);
  }

  .contact {
    position: absolute; right: 40px; color: var(--text-grey);
    font-weight: 300; font-size: 15px; line-height: 18px; text-align: right;
  }
  .contact--address { top: 197px; }
  .contact--lines { top: 251px; }
  .contact-line { display: flex; justify-content: flex-end; align-items: center; gap: 6px; }
  .contact-line svg { width: 12px; height: 12px; flex: none; }
</style>
</head>
<body>
  <section class="card card--front" aria-label="Card front">
    <div class="name-band">
      <div class="person">MARCO PELTIERI</div>
      <div class="role">Owner &amp; Manager</div>
    </div>
    <div class="brand"><span class="brand-square"></span><span>RWT Fittings Ltd</span></div>
    <div class="faint-mark" aria-hidden="true"></div>
    <div class="contact contact--address">
      <div>1407-5194 Linden Row</div>
      <div>Burnaby BC, V5H 2K9</div>
    </div>
    <div class="contact contact--lines">
      <div class="contact-line">1-604-551-8293
        <svg viewBox="0 0 12 12"><path d="M3 1 L5 3.5 L4 5 Q5 7.5 7 8 L8.5 7 L11 9 L10 11 Q4 11 1 3 Z" fill="var(--brand-blue)"/></svg>
      </div>
      <div class="contact-line">RWTFittings@mailbox-demo.com
        <svg viewBox="0 0 12 12"><rect x="1" y="2.5" width="10" height="7" fill="none" stroke="var(--brand-blue)" stroke-width="1.3"/><path d="M1 3 L6 6.5 L11 3" fill="none" stroke="var(--brand-blue)" stroke-width="1.3"/></svg>
      </div>
      <div class="contact-line">www.rwtfittings-demo.com
        <svg viewBox="0 0 12 12"><circle cx="6" cy="6" r="5" fill="none" stroke="var(--brand-blue)" stroke-width="1.2"/><ellipse cx="6" cy="6" rx="2.2" ry="5" fill="none" stroke="var(--brand-blue)" stroke-width="1"/><path d="M1 6 H11" stroke="var(--brand-blue)" stroke-width="1"/></svg>
      </div>
    </div>
  </section>

  <section class="card card--back" aria-label="Card back">
    <div class="brand"><span class="brand-square"></span><span>RWT Fittings Ltd</span></div>
  </section>
</body>
</html>
```